BrivoTerna. Lantern of the Steady Harvest. Business card

Professional business card for BrivoTerna (Lantern of the Steady Harvest)
My rationale: Strategy-> Execution-> Results-> Value that lead to the BrivoTerna name: We put the Lantern of the Steady Harvest.
We deliver value to our customers helping them at defining a good strategy (cyan arrow). 90% of well formulated strategies fail due to poor execution so we also consider strategical execution very important (green arrow). Due to the execution we obtain the results (blue arrow). Finally, the results provide feedback to redefine strategy, and the new strategy has to be executed and new results obtained providing new feedback and on and on. It's like a wheel that finally, must create corporate value: value for shareholders, staholders, employees, providers...-

Target Market(s)

CEOs and steering comitees , invewrnent funds

Industry/Entity Type

Business Consultant

Contact Information for Business Card

Teodoro Vinsquel
CEO & Founder
teodoro.vinsquel@brivoterna-example.com
Mobile: +34 655.803.912
www.brivoterna-example.com

Colors

Designer to choose colors to be used in the design.

Requirements
Nice to have
• Nice to hace the words: Strategy, execution, results
• Nice to vave the claim: Lantern of the Steady Harvest
• The three colors should be shown:
• cyan for STRATEGY
• green for EXECUTION
• blue for RESULTS
Should not have
• Complete black background

```html
<!DOCTYPE html>
<html lang="en">
<head>
<meta charset="UTF-8">
<title>BrivoTerna – Business Card</title>
<link rel="stylesheet" href="https://fonts.googleapis.com/css2?family=Ubuntu:wght@500;700&family=Open+Sans:wght@400;600&display=swap">
<style>
  :root {
    --stage: #2a2a2c;
    --card-white: #ffffff;
    --brand-cyan: #00aeef;
    --brand-blue: #0b3a96;
    --brand-green: #8dc63f;
    --ink: #2f2f33;
    --ink-soft: #5a5a60;
    --divider: #c9c9cd;
  }
  * { box-sizing: border-box; margin: 0; padding: 0; }
  html, body { width: 1200px; height: 960px; overflow: hidden; }
  body {
    background: var(--stage);
    font-family: "Open Sans", Arial, sans-serif;
    display: flex;
    flex-direction: column;
    align-items: center;
    justify-content: center;
    gap: 36px;
  }
  .card {
    position: relative;
    width: 760px;
    height: 434px;
    overflow: hidden;
  }

  /* Back side */
  .card--back {
    background: var(--brand-cyan);
    display: flex;
    flex-direction: column;
    align-items: center;
    justify-content: center;
    gap: 34px;
  }
  .back-mark {
    display: flex;
    align-items: center;
    gap: 18px;
  }
  .brand-dot {
    width: 30px; height: 30px;
    border-radius: 50%;
    background: var(--brand-blue);
  }
  .back-mark .brand-name {
    font-family: "Ubuntu", Arial, sans-serif;
    font-weight: 700;
    font-size: 64px;
    color: var(--brand-blue);
    letter-spacing: -1px;
  }
  .back-url {
    font-family: "Open Sans", Arial, sans-serif;
    font-weight: 600;
    font-size: 17px;
    letter-spacing: 3px;
    color: var(--brand-blue);
  }

  /* Front side */
  .card--front { background: var(--card-white); }
  .person {
    position: absolute;
    left: 44px; top: 128px;
  }
  .person__name {
    font-family: "Ubuntu", Arial, sans-serif;
    font-weight: 700;
    font-size: 28px;
    color: var(--brand-blue);
  }
  .person__role {
    font-size: 14px;
    color: var(--ink-soft);
    margin-top: 2px;
  }
  .rule-accent {
    position: absolute;
    left: 44px; top: 205px;
    width: 126px; height: 6px;
    background: var(--brand-blue);
  }
  .rule-line {
    position: absolute;
    left: 170px; right: 0; top: 209px;
    height: 2px;
    background: var(--brand-cyan);
  }
  .contacts {
    position: absolute;
    left: 44px; top: 228px;
    list-style: none;
    font-size: 15px;
    color: var(--ink);
    line-height: 24px;
  }
  .contacts li { display: flex; align-items: center; gap: 10px; }
  .contacts svg { width: 14px; height: 14px; flex: none; }
  .address-divider {
    position: absolute;
    left: 440px; top: 300px;
    width: 1px; height: 48px;
    background: var(--divider);
  }
  .address {
    position: absolute;
    left: 460px; top: 300px;
    font-size: 16px;
    line-height: 24px;
    color: var(--ink);
    font-style: normal;
  }
  .front-mark {
    position: absolute;
    right: 56px; top: 112px;
    display: flex;
    align-items: center;
    gap: 14px;
  }
  .front-mark .brand-name {
    font-family: "Ubuntu", Arial, sans-serif;
    font-weight: 700;
    font-size: 46px;
    color: var(--brand-blue);
    letter-spacing: -1px;
  }
  .front-mark .brand-dot { width: 22px; height: 22px; }
</style>
</head>
<body>

  <section class="card card--back" aria-label="Card back">
    <div class="back-mark">
      <span class="brand-dot"></span>
      <span class="brand-name">BrivoTerna</span>
    </div>
    <p class="back-url">www.brivoterna-example.com</p>
  </section>

  <section class="card card--front" aria-label="Card front">
    <div class="person">
      <h1 class="person__name">Teodoro Vinsquel</h1>
      <p class="person__role">CEO &amp; Founder</p>
    </div>

    <div class="front-mark">
      <span class="brand-dot"></span>
      <span class="brand-name">BrivoTerna</span>
    </div>

    <span class="rule-accent"></span>
    <span class="rule-line"></span>

    <ul class="contacts">
      <li>
        <svg viewBox="0 0 14 14" aria-hidden="true"><rect x="3" y="1" width="8" height="12" rx="1.5" fill="none" stroke="#00aeef" stroke-width="1.4"/></svg>
        +34 655.803.912
      </li>
      <li>
        <svg viewBox="0 0 14 14" aria-hidden="true"><rect x="1" y="3" width="12" height="8" fill="#0b3a96"/><path d="M1 3 L7 8 L13 3" fill="none" stroke="#fff" stroke-width="1"/></svg>
        teodoro.vinsquel@brivoterna-example.com
      </li>
      <li>
        <svg viewBox="0 0 14 14" aria-hidden="true"><circle cx="7" cy="7" r="6" fill="#00aeef"/><path d="M1 7 H13 M7 1 C4 4 4 10 7 13 M7 1 C10 4 10 10 7 13" fill="none" stroke="#fff" stroke-width="0.9"/></svg>
        www.brivoterna-example.com
      </li>
    </ul>

    <span class="address-divider"></span>
    <address class="address">
      Avda. Lumbrera 148<br>
      Valdoria , 08115, Spain
    </address>
  </section>

</body>
</html>
```